Veterinary Pylon

My veterinary clinic is not clearly visible from the street and I want to place a Pylon next to my driveway. I want a modern, elegant straight Design, the Photo shows the sheduled place. One can see the clinic on our Homepage: www.tailbright-vethaus.at
The last pictures are examples for pylones I like

Target Market(s)

the passing cars often miss my entry...I want to show where to turn left

Colors
3276b5
33a6d7
00a990

Requirements
Must have
• High value, simple elegance, size: 250cm (high) x 100cm (width)
Nice to have
• Our Logo, arrow(?)

A special Text is not necessary but this will be an option:

Biegen sie hier ab und wir biegen es wieder hin!
Should not have
• Too much Color, the colors I have chosen are the possible colors but it‘s not necessary to use them.

```html
<!DOCTYPE html>
<html lang="en">
<head>
<meta charset="utf-8">
<title>Tailbright Vethaus – Pylon</title>
<link rel="stylesheet" href="https://fonts.googleapis.com/css2?family=Roboto:wght@400;700;900&display=swap">
<style>
  :root {
    --navy: #124b93;
    --sky: #2ebde0;
    --arrow-dark: #1d6aa7;
    --white: #ffffff;
  }
  * { margin: 0; padding: 0; box-sizing: border-box; }
  html, body {
    width: 1200px;
    height: 3000px;
    overflow: hidden;
    background: var(--white);
  }
  .pylon {
    position: relative;
    width: 1200px;
    height: 3000px;
    background: var(--white);
    font-family: "Roboto", Arial, sans-serif;
    overflow: hidden;
  }
  .brand-name {
    position: absolute;
    top: 420px;
    left: 0;
    width: 1200px;
    text-align: center;
    color: var(--navy);
    font-weight: 900;
    font-size: 150px;
    line-height: 1.05;
    letter-spacing: 4px;
    text-transform: uppercase;
  }
  .direction-arrow {
    position: absolute;
    top: 1090px;
    left: 420px;
    width: 400px;
    height: 310px;
  }
  .chevron-band {
    position: absolute;
    top: 0;
    left: 0;
    width: 1200px;
    height: 3000px;
  }
  .contact {
    position: absolute;
    top: 1790px;
    left: 0;
    width: 1200px;
    text-align: center;
    color: var(--white);
  }
  .contact-title {
    font-weight: 700;
    font-size: 84px;
    line-height: 1.3;
    letter-spacing: 1px;
    text-transform: uppercase;
  }
  .contact-line {
    font-weight: 400;
    font-size: 64px;
    line-height: 115px;
  }
</style>
</head>
<body>
  <main class="pylon">
    <svg class="chevron-band" viewBox="0 0 1200 3000" aria-hidden="true">
      <polygon fill="var(--sky)" points="0,1328 596,1660 1200,1326 1200,3000 0,3000"/>
      <polygon fill="var(--navy)" points="0,1384 596,1714 1200,1384 1200,3000 0,3000"/>
    </svg>

    <h1 class="brand-name">Tailbright<br>Vethaus</h1>

    <svg class="direction-arrow" viewBox="0 0 400 310" role="img" aria-label="Arrow pointing left">
      <defs>
        <linearGradient id="arrow-fill" x1="0" y1="0" x2="1" y2="0">
          <stop offset="0" stop-color="var(--arrow-dark)"/>
          <stop offset="1" stop-color="var(--sky)"/>
        </linearGradient>
      </defs>
      <polygon fill="url(#arrow-fill)"
        points="19,152 157,17 157,60 60,138 372,138 372,166 60,166 157,245 157,288"/>
    </svg>

    <section class="contact">
      <h2 class="contact-title">Tailbright Vethaus</h2>
      <p class="contact-line">Lindenweg 12</p>
      <p class="contact-line">8570 Lindach an der Mur</p>
      <p class="contact-line">Tel:&nbsp; +43 3100 48217</p>
      <p class="contact-line">Mail: office@tailbright-vethaus.at</p>
    </section>
  </main>
</body>
</html>
```